Shopping centre customer engagement software website

We need a multi page site with :

*What we do.
*How it works.
*Benefits
* Case study
* Testimonial
* Business login (we provide link to business portal)
* Consumer login (we provide link to consumer site)
* Book a demo
* Contact us

We want it to be clean and crisp and very self explanatory with little clutter. We are thinking white but are open to what ever looks the best.
Updates

Wordpress is preferred

Need extra days to review

Target Market(s)

Shopping centre managers and retail property companies

Coding

Coded - Design and coding required

Number of Pages Required

5+ page

Font styles to use
Sans Serif

Colors
ffffff

Requirements
Must have
• As listed above and must be responsive! Checkout our existing site for the text to be included (will be edited but it’ll give you an idea) www.vostrelink.com

```html
<!DOCTYPE html>
<html lang="en">
<head>
<meta charset="utf-8">
<title>Vostrelink — Shopping centre customer engagement</title>
<link rel="stylesheet" href="https://fonts.googleapis.com/css2?family=Arimo:wght@400;700&display=swap">
<style>
  :root {
    --white: #ffffff;
    --ink: #222326;
    --ink-soft: #4a4c50;
    --muted: #7b7e84;
    --bar: #f1f1f2;
    --bar-line: #dcdcde;
    --accent: #5fc3df;
    --hero-dark: #2a1a14;
    --hero-warm: #6b3a26;
    --hero-red: #9a2f2c;
    --hero-blue: #2f4a72;
  }
  * { box-sizing: border-box; margin: 0; padding: 0; }
  html, body { width: 1200px; height: 676px; overflow: hidden; background: var(--white); }
  body { font-family: "Arimo", Arial, sans-serif; color: var(--ink); }

  .site { width: 1200px; height: 676px; position: relative; background: var(--white); }

  .hero { position: relative; height: 488px; overflow: hidden; }
  .hero-photo {
    position: absolute; inset: 0;
    background:
      radial-gradient(ellipse 30% 45% at 78% 55%, var(--hero-blue) 0%, transparent 70%),
      radial-gradient(ellipse 22% 40% at 92% 45%, var(--hero-red) 0%, transparent 75%),
      radial-gradient(ellipse 35% 40% at 30% 30%, #8a5a34 0%, transparent 75%),
      linear-gradient(180deg, #4a2c1e 0%, var(--hero-warm) 40%, var(--hero-dark) 100%);
  }

  .masthead {
    position: absolute; top: 0; left: 0; right: 0; height: 64px;
    display: flex; align-items: center; padding: 0 26px;
    border-bottom: 1px solid rgba(255,255,255,0.35);
  }
  .brand { display: flex; align-items: center; gap: 10px; width: 300px; }
  .brand-dot { width: 34px; height: 34px; border-radius: 50%; background: var(--white); opacity: 0.9; }
  .brand-name { font-size: 24px; font-weight: 400; color: var(--white); letter-spacing: 2px; }

  .main-nav { display: flex; gap: 28px; margin-left: 8px; }
  .main-nav a { color: var(--white); text-decoration: none; font-size: 12px; letter-spacing: 0.2px; }

  .logins { margin-left: auto; display: flex; gap: 8px; }
  .login-btn {
    font-size: 12px; padding: 7px 16px; border-radius: 16px;
    text-decoration: none; border: 2px solid var(--white);
  }
  .login-btn.consumer { color: var(--white); }
  .login-btn.business { color: var(--ink); background: var(--white); }

  .subnav {
    height: 34px; background: var(--bar); border-bottom: 1px solid var(--bar-line);
    display: flex; align-items: center; padding: 0 40px; font-size: 12px;
  }
  .subnav-label { color: var(--ink-soft); margin-right: 12px; }
  .subnav a { color: var(--muted); text-decoration: none; margin-right: 20px; }
  .social { margin-left: auto; display: flex; align-items: center; gap: 18px; }
  .social-mark { width: 13px; height: 13px; border-radius: 2px; background: #9da0a6; }

  .intro { text-align: center; padding-top: 20px; }
  .intro-title { font-size: 19px; font-weight: 400; line-height: 1.3; color: var(--ink); }
  .intro-sub { font-size: 11px; color: var(--ink-soft); margin-top: 9px; }
  .demo-btn {
    display: inline-flex; align-items: center; gap: 8px; margin-top: 12px;
    border: 1.5px solid var(--accent); border-radius: 18px; padding: 8px 16px;
    color: var(--accent); font-size: 12px; font-weight: 700; text-decoration: none;
  }
</style>
</head>
<body>
<div class="site">
  <header class="hero">
    <div class="hero-photo" role="img" aria-label="Two friends at a café table in a shopping centre looking at a phone, shop shelves behind"></div>
    <div class="masthead">
      <div class="brand"><span class="brand-dot"></span><span class="brand-name">VOSTRELINK</span></div>
      <nav class="main-nav">
        <a href="#">HOW IT WORKS</a>
        <a href="#">BENEFITS</a>
        <a href="#">WHAT WE DO</a>
        <a href="#">CASE STUDY</a>
      </nav>
      <div class="logins">
        <a class="login-btn consumer" href="#">Consumer login</a>
        <a class="login-btn business" href="#">Business login</a>
      </div>
    </div>
  </header>

  <div class="subnav">
    <span class="subnav-label">Learn More:</span>
    <a href="#">Our Company</a>
    <a href="#">Testimonials</a>
    <a href="#">Careers</a>
    <a href="#">Help &amp; Contact</a>
    <div class="social">
      <span class="social-mark"></span>
      <span class="social-mark"></span>
      <span class="social-mark"></span>
      <svg width="13" height="13" viewBox="0 0 13 13" aria-label="Search"><circle cx="5.5" cy="5.5" r="4" fill="none" stroke="#9da0a6" stroke-width="1.6"/><line x1="8.5" y1="8.5" x2="12" y2="12" stroke="#9da0a6" stroke-width="1.8"/></svg>
    </div>
  </div>

  <section class="intro">
    <h1 class="intro-title">Delight your shoppers, impress your tenants and provide your<br>landlords with accurate detailed data in real time</h1>
    <p class="intro-sub">See some of the features below and learn why businesses trust Vostrelink</p>
    <a class="demo-btn" href="#"><svg width="9" height="10" viewBox="0 0 9 10"><path d="M0 0 L9 5 L0 10 Z" fill="#5fc3df"/></svg>BOOK A DEMO</a>
  </section>
</div>
</body>
</html>
```